Corporate Business Card

Very professional, Modern, Not to busy, include phone address email, website
(253) 617-4930, 18761 52nd Avenue S, Kent, WA 98047, martin@plumlinegroup.com, varkoworks.com

Target Market(s)

Manufacturing

Industry/Entity Type

Aero, machining, manufacturing, Off road racing

Contact Information for Business Card

Phone, address email, website

```html
<!DOCTYPE html>
<html lang="en">
<head>
<meta charset="utf-8">
<title>Varko Works – Business Card</title>
<link href="https://fonts.googleapis.com/css2?family=Exo+2:wght@400;600;700&display=swap" rel="stylesheet">
<style>
  :root {
    --navy: #1b3570;
    --red: #d62229;
    --wine: #7a2a4c;
    --paper: #ffffff;
    --backdrop: #e4e5e7;
    --font: "Exo 2", sans-serif;
  }
  * { margin: 0; padding: 0; box-sizing: border-box; }
  html, body {
    width: 1200px; height: 900px; overflow: hidden;
    background: var(--backdrop);
    font-family: var(--font);
  }
  .stage { position: relative; width: 1200px; height: 900px; }

  .card {
    position: absolute;
    top: 217px;
    width: 309px;
    height: 501px;
    box-shadow: 2px 3px 4px rgba(0,0,0,0.35);
    overflow: hidden;
  }

  /* Front */
  .card-front {
    left: 279px;
    border-radius: 0 60px 0 60px;
    background: linear-gradient(225deg, var(--red) 0%, #a6243a 30%, var(--wine) 58%, var(--navy) 100%);
  }
  .card-front .brand-name {
    position: absolute;
    left: 38px;
    top: 380px;
    font-size: 34px;
    font-weight: 700;
    color: var(--paper);
    letter-spacing: 1px;
    text-transform: uppercase;
    white-space: nowrap;
  }

  /* Back */
  .card-back {
    left: 617px;
    border-radius: 60px 0 60px 0;
    background: var(--paper);
  }
  .card-back .brand-name {
    position: absolute;
    left: 39px;
    top: 336px;
    top: 120px;
    font-size: 36px;
    font-weight: 700;
    color: var(--navy);
    letter-spacing: 1px;
    text-transform: uppercase;
    white-space: nowrap;
  }

  .person {
    position: absolute;
    left: 39px;
    top: 295px;
  }
  .person-name {
    font-size: 18px;
    font-weight: 700;
    color: var(--navy);
    text-transform: uppercase;
    letter-spacing: 0.3px;
    line-height: 20px;
  }
  .person-title {
    font-size: 14px;
    font-weight: 400;
    color: var(--red);
    line-height: 16px;
  }

  .contact-list {
    position: absolute;
    left: 39px;
    top: 351px;
    list-style: none;
  }
  .contact-item {
    display: flex;
    align-items: center;
    gap: 5px;
    font-size: 14px;
    color: var(--navy);
    line-height: 18px;
    white-space: nowrap;
  }
  .contact-item svg { width: 13px; height: 13px; flex: none; }

  .address {
    position: absolute;
    left: 39px;
    top: 428px;
    display: flex;
    align-items: flex-start;
    gap: 6px;
    font-size: 14px;
    color: var(--navy);
    line-height: 18px;
    font-style: normal;
  }
  .address svg { width: 13px; height: 19px; flex: none; }
</style>
</head>
<body>
<main class="stage">

  <section class="card card-front" aria-label="Card front">
    <div class="brand-name">Varko Works</div>
  </section>

  <section class="card card-back" aria-label="Card back">
    <div class="brand-name">Varko Works</div>

    <div class="person">
      <div class="person-name">Daniel Reyes</div>
      <div class="person-title">Managing Director</div>
    </div>

    <ul class="contact-list">
      <li class="contact-item">
        <svg viewBox="0 0 24 24" aria-hidden="true"><path fill="#d62229" d="M6.6 10.8a15.1 15.1 0 0 0 6.6 6.6l2.2-2.2a1 1 0 0 1 1-.25 11.4 11.4 0 0 0 3.6.57 1 1 0 0 1 1 1V20a1 1 0 0 1-1 1A17 17 0 0 1 3 4a1 1 0 0 1 1-1h3.5a1 1 0 0 1 1 1c0 1.25.2 2.45.57 3.57a1 1 0 0 1-.25 1z"/></svg>
        (253) 617-4930
      </li>
      <li class="contact-item">
        <svg viewBox="0 0 24 24" aria-hidden="true"><rect x="2" y="5" width="20" height="14" fill="#d62229"/><path d="M2 5l10 8 10-8" fill="none" stroke="#fff" stroke-width="1.6"/></svg>
        martin@plumlinegroup.com
      </li>
      <li class="contact-item">
        <svg viewBox="0 0 24 24" aria-hidden="true"><g fill="none" stroke="#d62229" stroke-width="2"><circle cx="12" cy="12" r="10"/><ellipse cx="12" cy="12" rx="4.5" ry="10"/><path d="M2 12h20M4 7h16M4 17h16"/></g></svg>
        www.varkoworks.com
      </li>
    </ul>

    <address class="address">
      <svg viewBox="0 0 16 24" aria-hidden="true"><path fill="#d62229" d="M8 0a8 8 0 0 0-8 8c0 6 8 16 8 16s8-10 8-16a8 8 0 0 0-8-8zm0 11a3 3 0 1 1 0-6 3 3 0 0 1 0 6z"/></svg>
      <span>18761 52nd Avenue S<br>Kent, WA 98047</span>
    </address>
  </section>

</main>
</body>
</html>
```